Business Card Design Project - Brindle Works

We need a new business card that fits with our new logo. We are a social media agency and consultancy operating in China. We want a fresh and strong business card. Our cards need to be two-sided as we have both English and Chinese language names and addresses on the card, but as with our current business card this does not need to be a mirror-image. Our thoughts go out to a white card on the front where the logo/name is and then using the logo colours for different coloured back-grounds. i.e that the back of the biz card works with the four different colours in the logo.

Attached is the new logo, and also a copy of our old business cards.

Target Market(s)

CEO's, CMO's. media and advertising professionals

Industry/Entity Type

Business

Requirements
Must have
• inclusion of both Chinese and English language
Nice to have
• four different colored versions of the back of the biz card. Our logo has four colors and each of these colors we would like to have a version of.

```html
<!DOCTYPE html>
<html lang="en">
<head>
<meta charset="utf-8">
<title>Brindle Works – Business Card</title>
<link rel="stylesheet" href="https://fonts.googleapis.com/css2?family=Open+Sans:wght@400;600;700&family=Noto+Sans+SC:wght@400;500&display=swap">
<style>
  :root {
    --paper: #ffffff;
    --ink: #141414;
    --ink-soft: #3a3a3a;
    --brand-green: #8dc63f;
    --brand-orange: #f15a22;
    --card-shadow: 4px 7px 12px rgba(0, 0, 0, 0.32);
  }
  * { margin: 0; padding: 0; box-sizing: border-box; }
  html, body {
    width: 1200px;
    height: 840px;
    overflow: hidden;
    background: var(--paper);
  }
  .sheet {
    position: relative;
    width: 1200px;
    height: 840px;
    font-family: "Open Sans", Arial, sans-serif;
  }
  .card {
    position: absolute;
    top: 262px;
    width: 517px;
    height: 317px;
    box-shadow: var(--card-shadow);
    overflow: hidden;
  }
  .card--front { left: 58px; background: var(--paper); color: var(--ink); }
  .card--back { left: 633px; background: var(--brand-green); color: var(--paper); }

  .wordmark {
    position: absolute;
    top: 44px;
    right: 28px;
    display: flex;
    align-items: center;
    gap: 12px;
  }
  .wordmark__name {
    font-size: 46px;
    font-weight: 700;
    letter-spacing: -1px;
    line-height: 1;
  }
  .wordmark__dot {
    width: 14px;
    height: 14px;
    background: var(--brand-orange);
  }
  .card--front .wordmark__name { color: var(--ink); }
  .card--back .wordmark__name { color: var(--paper); }

  .holder {
    position: absolute;
    left: 29px;
    top: 172px;
  }
  .holder__name {
    font-size: 26px;
    font-weight: 400;
    line-height: 1.1;
    letter-spacing: -0.3px;
  }
  .holder__role {
    font-size: 14px;
    color: var(--ink-soft);
    line-height: 1.2;
  }

  .contact {
    position: absolute;
    left: 29px;
    top: 243px;
    font-size: 13px;
    line-height: 16.5px;
    border-collapse: collapse;
  }
  .contact td { padding: 0; }
  .contact__label {
    width: 61px;
    color: var(--brand-green);
    font-weight: 600;
  }
  .contact__value { color: var(--ink-soft); }

  .web-band {
    position: absolute;
    left: 280px;
    right: 0;
    top: 247px;
    height: 41px;
    background: var(--brand-green);
    color: var(--paper);
    font-size: 20px;
    line-height: 41px;
    padding-left: 10px;
  }

  .holder-cn {
    position: absolute;
    left: 29px;
    top: 178px;
    display: flex;
    align-items: baseline;
    gap: 10px;
    font-family: "Noto Sans SC", "Open Sans", sans-serif;
  }
  .holder-cn__name { font-size: 26px; font-weight: 500; letter-spacing: 2px; }
  .holder-cn__role { font-size: 14px; }

  .address {
    position: absolute;
    top: 244px;
    font-size: 13px;
    line-height: 16.5px;
  }
  .address--cn {
    left: 29px;
    font-family: "Noto Sans SC", "Open Sans", sans-serif;
    font-size: 12.5px;
  }
  .address--en { left: 269px; }
</style>
</head>
<body>
<main class="sheet">

  <section class="card card--front" aria-label="Card front, English">
    <div class="wordmark">
      <span class="wordmark__name">Brindle Works</span>
      <span class="wordmark__dot"></span>
    </div>

    <div class="holder">
      <p class="holder__name">Daniel Hartley</p>
      <p class="holder__role">managing director</p>
    </div>

    <table class="contact">
      <tr><td class="contact__label">email:</td><td class="contact__value">daniel@brindleworks.com</td></tr>
      <tr><td class="contact__label">skype:</td><td class="contact__value">danielbeijing</td></tr>
      <tr><td class="contact__label">mobile:</td><td class="contact__value">+86 13900004821</td></tr>
    </table>

    <div class="web-band">www.brindleworks.com</div>
  </section>

  <section class="card card--back" aria-label="Card back, Chinese and address">
    <div class="wordmark">
      <span class="wordmark__name">Brindle Works</span>
      <span class="wordmark__dot"></span>
    </div>

    <div class="holder-cn" lang="zh">
      <span class="holder-cn__name">韩德林</span>
      <span class="holder-cn__role">董事总经理</span>
    </div>

    <p class="address address--cn" lang="zh">
      林荫商务中心套房C310<br>
      朝阳区光华东路中段光华路<br>
      林荫大厦 · 北京 (100020)
    </p>

    <p class="address address--en">
      Linden Tree Business Centre,<br>
      Suite C310, Guanghua East Rd<br>
      Chaoyang District, Beijing 100020
    </p>
  </section>

</main>
</body>
</html>
```